Clearing Your Slate - Banner Ad for TH Website

I need a banner ad for a book I'm selling.

The book is about Clearing Your Slate, that is a County Court Judgment, from a credit report.

I have two websites. I want the banner ad to appear on
www.thorncaldwell.co.uk

It will then link to the new site: https://debtslatecleaner.co.uk/

The first site already has a lot of traffic from visitors wanting to remove a CCJ. The purpose of that first site was originally for visitors to become clients of the law firm. However, most visitors can't afford legal advice and so I'd like to offer them the book instead.

I would like to see designs that use the colour green. The final design should communicate financial freedom, simplicity and trustworthiness.

Target Market(s)

Individuals who have discovered a CCJ on their credit report

Industry/Entity Type

Law

Font styles to use
Sans Serif

Colors
0054AA
0677BA
7BADD7
CADEEF
E8F1F8
0094D4
00A9DD
6FCCEA
C7EBF8
E9F6FB
00AB8E
00BBA5
67D7C9
C6EFE9
E9F9F6

Requirements
Must have
• Must fit at the end of a blog article, such as this one https://www.thorncaldwell.co.uk/ccj-wrong-address/

```html
<!DOCTYPE html>
<html lang="en">
<head>
<meta charset="utf-8">
<title>Clearing Your Slate – Banner</title>
<link rel="stylesheet" href="https://fonts.googleapis.com/css2?family=Montserrat:wght@400;500;700;800;900&display=swap">
<style>
  :root {
    --page-bg: #9b9b9b;
    --green: #43a143;
    --green-light: #4fb04f;
    --green-shadow: #2d7a2d;
    --orange: #f0900a;
    --orange-light: #f6bb62;
    --white: #ffffff;
    --product-top: #f4f5f6;
    --product-bottom: #dfe2e5;
  }
  * { margin: 0; padding: 0; box-sizing: border-box; }
  html, body {
    width: 1200px;
    height: 800px;
    overflow: hidden;
    background: var(--page-bg);
    font-family: "Montserrat", sans-serif;
  }
  .banner {
    position: absolute;
    left: 94px;
    top: 192px;
    width: 1012px;
    height: 416px;
    overflow: hidden;
    background: var(--green);
  }
  .banner-backdrop {
    position: absolute;
    inset: 0;
    width: 100%;
    height: 100%;
  }
  .headline {
    position: absolute;
    color: var(--white);
    font-weight: 800;
    line-height: 1;
    text-shadow: 3px 3px 0 var(--green-shadow);
    white-space: nowrap;
  }
  .headline-need { left: 126px; top: 34px; font-size: 47px; }
  .headline-remove { left: 59px; top: 62px; font-size: 86px; letter-spacing: -1px; }
  .headline-article { left: 99px; top: 150px; font-size: 30px; }
  .headline-ccj { left: 124px; top: 140px; font-size: 94px; letter-spacing: -2px; }

  .subline {
    position: absolute;
    left: 64px;
    top: 242px;
    padding-left: 15px;
    border-left: 2px solid var(--white);
    color: var(--white);
    line-height: 1.2;
  }
  .subline-strong { display: block; font-weight: 700; font-size: 23px; }
  .subline-light { display: block; font-weight: 400; font-size: 23px; padding-left: 3px; }

  .cta-button {
    position: absolute;
    left: 63px;
    top: 323px;
    width: 284px;
    height: 51px;
    border: 2px solid var(--white);
    border-radius: 26px;
    background: var(--orange);
    color: var(--white);
    font-weight: 700;
    font-size: 22px;
    display: flex;
    align-items: center;
    justify-content: center;
    text-decoration: none;
  }

  .product-visual {
    position: absolute;
    left: 509px;
    top: 31px;
    width: 450px;
    height: 354px;
    border-radius: 6px;
    background: linear-gradient(160deg, var(--product-top), var(--product-bottom));
  }
</style>
</head>
<body>
  <section class="banner">
    <svg class="banner-backdrop" viewBox="0 0 1012 416" preserveAspectRatio="none" aria-hidden="true">
      <polygon points="0,250 0,416 215,416" fill="var(--green-light)"/>
      <polygon points="460,0 533,0 713,416 640,416" fill="var(--orange-light)"/>
      <polygon points="533,0 1012,0 1012,416 713,416" fill="var(--orange)"/>
    </svg>

    <span class="headline headline-need">Need to</span>
    <span class="headline headline-remove">Remove</span>
    <span class="headline headline-article">a</span>
    <span class="headline headline-ccj">CCJ?</span>

    <p class="subline">
      <span class="subline-strong">Find out how with this simple</span>
      <span class="subline-light">jargon-free guide</span>
    </p>

    <a class="cta-button" href="https://debtslatecleaner.co.uk/">Get Your Copy Now</a>

    <div class="product-visual" role="img" aria-label="The book Clearing Your Slate by Owen Hartley shown as a paperback, on a tablet and on a phone"></div>
  </section>
</body>
</html>
```